Zolvana Stationary and Branding Documents

Corporate Identity Branding stationary needed for IT Recruiting Firm.

I already have a Logo, business cards and website. I need to get designs completed for the remaining corporate identity documents.

The documentation should use similar colors as my website and business card. The designs should modern and clean.

http://zolvanaworks.example/

Target Market(s)

Information Technology Industry

Industry/Entity Type

Information Technology

Colors
3377b5
0255a3
fbee3e
f78f20
f37122
33a6d7
000000
0592cd

Requirements
Must have
• Letter Head
• Folder Design
• PowerPoint Design
• Invoice
• Envelope
Nice to have
• Proposal
• Flyer
• Brochure
Should not have
• Logo
• Business Cards
• Website

```html
<!DOCTYPE html>
<html lang="en">
<head>
<meta charset="utf-8">
<title>Zolvana Folder Design</title>
<link href="https://fonts.googleapis.com/css2?family=Cinzel:wght@500&family=Open+Sans:wght@400;600;700&display=swap" rel="stylesheet">
<style>
  :root {
    --brand-blue: #0b5fa5;
    --brand-blue-deep: #0255a3;
    --brand-blue-light: #3377b5;
    --brand-orange: #f37122;
    --brand-orange-light: #f78f20;
    --photo-cool: #cfe3f0;
    --photo-warm: #eef1f4;
    --shadow-grey: #b9c3cc;
    --paper: #ffffff;
    --stage: #e9edf1;
  }
  html, body {
    margin: 0;
    padding: 0;
    width: 1200px;
    height: 847px;
    overflow: hidden;
    background: var(--stage);
  }
  .folder-spread {
    position: absolute;
    left: 140px;
    top: 113px;
    display: flex;
    box-shadow: 0 10px 30px rgba(0, 0, 0, 0.18);
  }
  .folder-panel {
    display: block;
    width: 460px;
    height: 620px;
  }
  .company-name {
    font-family: "Open Sans", sans-serif;
    font-weight: 600;
    fill: var(--paper);
  }
  .company-descriptor {
    font-family: "Open Sans", sans-serif;
    font-weight: 400;
    fill: var(--paper);
  }
  .tagline {
    font-family: "Cinzel", serif;
    font-weight: 500;
    fill: var(--paper);
  }
  .body-copy {
    font-family: "Open Sans", sans-serif;
    font-weight: 700;
    fill: var(--paper);
    font-size: 7.6px;
    letter-spacing: 0.2px;
  }
  .contact-line {
    font-family: "Open Sans", sans-serif;
    font-weight: 400;
    fill: var(--paper);
    font-size: 7.5px;
  }
</style>
</head>
<body>
  <main class="folder-spread">
    <!-- Back cover -->
    <svg class="folder-panel back-cover" viewBox="0 0 460 620" xmlns="http://www.w3.org/2000/svg">
      <defs>
        <linearGradient id="backPhotoTone" x1="0" y1="0" x2="1" y2="1">
          <stop offset="0" stop-color="var(--photo-warm)"/>
          <stop offset="1" stop-color="var(--photo-cool)"/>
        </linearGradient>
        <linearGradient id="blueField" x1="0" y1="0" x2="1" y2="1">
          <stop offset="0" stop-color="var(--brand-blue-light)"/>
          <stop offset="1" stop-color="var(--brand-blue-deep)"/>
        </linearGradient>
      </defs>
      <rect class="blue-field" width="460" height="620" fill="url(#blueField)"/>
      <path class="photo-area" role="img" aria-label="Photo of a smiling businesswoman with two colleagues reviewing a folder in a bright office"
            d="M0 6 H460 V6 C420 140 330 220 210 250 C110 275 40 300 0 400 Z" fill="url(#backPhotoTone)"/>
      <path class="curve-shadow" d="M460 6 C420 140 330 220 210 250 C110 275 40 300 0 400 L0 412 C45 312 115 287 214 262 C336 232 428 150 460 20 Z" fill="var(--shadow-grey)"/>
      <rect class="top-rule" width="460" height="6" fill="var(--brand-orange)"/>

      <g class="company-block">
        <circle cx="170" cy="464" r="6" fill="var(--brand-orange)"/>
        <text class="company-name" x="182" y="474" font-size="28">Zolvana</text>
        <text class="company-descriptor" x="230" y="492" font-size="9" text-anchor="middle">Business Solution LLC</text>
      </g>
      <text class="tagline" x="230" y="516" font-size="14" text-anchor="middle">JOIN THE ELITE</text>
      <text class="body-copy" x="230" y="534" text-anchor="middle">ELITE IT TALENT IS NO ACCIDENT. IT TAKES PERSONAL</text>
      <text class="body-copy" x="230" y="546" text-anchor="middle">DRIVE AND SMARTS, PLUS SMART CAREER COUNSELING. DO YOU HAVE WHAT IT TAKES? IF YOU DO,</text>
      <text class="body-copy" x="230" y="558" text-anchor="middle">WE PROVIDE MENTORING AND COUNSEL, AND WE'LL STAY WITH YOU THROUGHOUT YOUR CAREER.</text>

      <rect class="contact-band" y="578" width="460" height="42" fill="var(--brand-orange)"/>
      <g class="contact-details">
        <circle cx="12" cy="599" r="3.5" fill="none" stroke="var(--paper)" stroke-width="1.2"/>
        <circle cx="12" cy="599" r="1.2" fill="var(--paper)"/>
        <text class="contact-line" x="19" y="602" textLength="140" lengthAdjust="spacingAndGlyphs">Two Harbor Plaza 410 Linden Avenue</text>
        <rect x="167" y="595.5" width="7" height="6" rx="1.5" fill="var(--paper)"/>
        <text class="contact-line" x="177" y="602" textLength="42" lengthAdjust="spacingAndGlyphs">5550142876</text>
        <rect x="227" y="595.5" width="8" height="6" fill="none" stroke="var(--paper)" stroke-width="1"/>
        <text class="contact-line" x="238" y="602" textLength="104" lengthAdjust="spacingAndGlyphs">info@zolvanaworks.example</text>
        <circle cx="352" cy="599" r="3" fill="var(--paper)"/>
        <text class="contact-line" x="358" y="602" textLength="84" lengthAdjust="spacingAndGlyphs">zolvanaworks.example</text>
      </g>
    </svg>

    <!-- Front cover -->
    <svg class="folder-panel front-cover" viewBox="0 0 460 620" xmlns="http://www.w3.org/2000/svg">
      <defs>
        <linearGradient id="frontPhotoTone" x1="0" y1="0" x2="1" y2="1">
          <stop offset="0" stop-color="var(--photo-cool)"/>
          <stop offset="1" stop-color="var(--photo-warm)"/>
        </linearGradient>
        <linearGradient id="frontBlue" x1="0" y1="0" x2="1" y2="1">
          <stop offset="0" stop-color="var(--brand-blue)"/>
          <stop offset="1" stop-color="var(--brand-blue-deep)"/>
        </linearGradient>
      </defs>
      <rect class="photo-area" role="img" aria-label="Photo of three business colleagues smiling and discussing work at a desk"
            width="460" height="620" fill="url(#frontPhotoTone)"/>
      <path class="curve-shadow" d="M0 0 H460 V200 C430 300 340 330 230 350 C110 372 40 400 0 470 Z" fill="var(--shadow-grey)"/>
      <path class="blue-field" d="M0 0 H460 V188 C428 290 338 318 226 338 C108 360 38 388 0 458 Z" fill="url(#frontBlue)"/>
      <rect class="top-rule" width="460" height="6" fill="var(--brand-orange)"/>

      <g class="company-block">
        <circle cx="140" cy="101" r="9" fill="var(--brand-orange)"/>
        <text class="company-name" x="158" y="116" font-size="44">Zolvana</text>
        <text class="company-descriptor" x="230" y="144" font-size="13" text-anchor="middle">Business Solution LLC</text>
      </g>

      <rect class="tagline-band" y="572" width="460" height="48" fill="var(--brand-orange)"/>
      <text class="tagline" x="230" y="602" font-size="16" text-anchor="middle">JOIN THE ELITE</text>
    </svg>
  </main>
</body>
</html>
```